Harrow Grading LLC business card design

Excavation company business cards

Contact Information for Business Card

Harrow Grading LLC cell phone 208-417-6290 office phone 208-319-4856 harrowgradingllc@maplecove.com Driveways, site prep, retaining walls, septic systems, rock delivery

Colors

Designer to choose colors to be used in the design.

```html
<!DOCTYPE html>
<html lang="en">
<head>
<meta charset="utf-8">
<title>Harrow Grading LLC – Business Card</title>
<link rel="stylesheet" href="https://fonts.googleapis.com/css2?family=Lato:wght@400;700;900&family=Roboto:wght@400&display=swap">
<style>
  :root {
    --page-bg: #2b2b2c;
    --card-bg: #1e1f20;
    --orange: #f07a1c;
    --grey-text: #a9a9ab;
    --rule: #6c6c6e;
    --pattern-dark: #141414;
    --pattern-light: #5a5a5c;
  }
  * { box-sizing: border-box; margin: 0; padding: 0; }
  html, body {
    width: 1200px; height: 1108px; overflow: hidden;
    background: var(--page-bg);
  }
  .canvas {
    position: relative; width: 1200px; height: 1108px;
    display: flex; justify-content: center; align-items: center; gap: 60px;
  }
  .card {
    width: 440px; height: 770px;
    background: var(--card-bg);
    border-radius: 22px;
    position: relative;
    overflow: hidden;
    box-shadow: 0 18px 40px rgba(0,0,0,0.45);
  }

  /* Front */
  .card-front {
    font-family: "Lato", sans-serif;
    text-align: center;
    color: var(--grey-text);
  }
  .brand {
    position: absolute; top: 180px; left: 0; right: 0;
    display: flex; flex-direction: column; align-items: center; gap: 18px;
  }
  .brand-mark {
    width: 18px; height: 18px; background: var(--orange);
  }
  .brand-name {
    font-weight: 900; font-size: 38px; letter-spacing: 1px;
    color: var(--orange); text-transform: uppercase; line-height: 1.1;
  }
  .person {
    position: absolute; top: 405px; left: 0; right: 0;
  }
  .person-name {
    font-weight: 700; font-size: 27px; color: var(--orange);
    text-transform: uppercase; letter-spacing: 0.5px;
  }
  .person-title { font-size: 21px; margin-top: 2px; }
  .contact-icons {
    position: absolute; top: 482px; left: 50px; right: 50px;
    display: flex; align-items: center; gap: 8px;
  }
  .contact-icons .rule { flex: 1; height: 1px; background: var(--rule); }
  .icon {
    width: 36px; height: 36px; border-radius: 6px; background: var(--orange);
    display: flex; align-items: center; justify-content: center;
  }
  .contact-lines {
    position: absolute; top: 538px; left: 0; right: 0;
    font-size: 20px; line-height: 1.45;
  }
  .divider {
    position: absolute; top: 646px; left: 70px; right: 70px;
    height: 1px; background: var(--rule);
  }
  .address {
    position: absolute; top: 664px; left: 0; right: 0;
    font-size: 20px; line-height: 1.45;
  }

  /* Back */
  .pattern {
    position: absolute; inset: 0;
    background: linear-gradient(210deg, var(--pattern-light) 0%, #2e2e30 45%, var(--pattern-dark) 100%);
  }
  .services {
    position: absolute; left: 0; right: 0; bottom: 110px;
    font-family: "Roboto", sans-serif; font-size: 21px; color: var(--grey-text);
    text-align: center; line-height: 1.5;
  }
  .services .dot { color: var(--orange); padding: 0 4px; }
</style>
</head>
<body>
<main class="canvas">

  <section class="card card-front" aria-label="Business card front">
    <div class="brand">
      <span class="brand-mark"></span>
      <span class="brand-name">Harrow Grading LLC</span>
    </div>

    <div class="person">
      <p class="person-name">Daniel Mercer</p>
      <p class="person-title">Managing Director</p>
    </div>

    <div class="contact-icons">
      <span class="rule"></span>
      <span class="icon" aria-label="Cell phone">
        <svg width="20" height="22" viewBox="0 0 20 22"><rect x="5" y="1" width="10" height="20" rx="2" fill="none" stroke="#1e1f20" stroke-width="2"/><circle cx="10" cy="17" r="1.3" fill="#1e1f20"/></svg>
      </span>
      <span class="icon" aria-label="Office phone">
        <svg width="22" height="20" viewBox="0 0 22 20"><path d="M2 7c0-3 4-5 9-5s9 2 9 5l-4 1-1-3H7L6 8z" fill="#1e1f20"/><rect x="5" y="10" width="12" height="8" rx="2" fill="#1e1f20"/></svg>
      </span>
      <span class="icon" aria-label="Email">
        <svg width="22" height="16" viewBox="0 0 22 16"><rect x="1" y="1" width="20" height="14" fill="none" stroke="#1e1f20" stroke-width="2"/><path d="M1 1l10 8 10-8" fill="none" stroke="#1e1f20" stroke-width="2"/></svg>
      </span>
      <span class="rule"></span>
    </div>

    <div class="contact-lines">
      <p>208-417-6290</p>
      <p>208-319-4856</p>
      <p>harrowgradingllc@maplecove.com</p>
    </div>

    <div class="divider"></div>

    <div class="address">
      <p>421, Address line here</p>
      <p>45452,Country Name</p>
    </div>
  </section>

  <section class="card card-back" aria-label="Business card back">
    <div class="pattern" role="img" aria-label="Repeating pattern of excavator silhouettes fading from grey to black"></div>
    <p class="services">
      Driveways<span class="dot">●</span>Site prep<span class="dot">●</span>Retaining walls<br>
      Septic systems<span class="dot">●</span>Rock delivery
    </p>
  </section>

</main>
</body>
</html>
```